elegant beautiful Hang tag for a novelty makeup towel

It's a black hand towel in the shape of a little black dress. it is called PETAL CHARM TOWEL, it is a CLEAN SLATE MAKEUP TOWEL. (doesn't show our makeup stains) Made in USA

Target Market(s)

ALL Women , Makeup artists, novelty THIS WILL BE IN THE HALVERGATE STORES AND KESTRELMOOR STORES.

Industry/Entity Type

Makeup

Contact Information for Business Card

I actually need a hang tag for a homemade handmade towel. I have a logo that I want on the tag and know what we want to say on it, on back needs to say "The essential to every girl's wardrobe. So when the little black dress comes off, our PETAL CHARM TOWEL is there to help you wash your day away. Include website www.petalcharmtowel.com OH INCLUDE TM (trademark sign next to logo please. Also, in small print on back from the makers of THE ORIGINAL CLEAN SLATE MAKEUP TOWEL. handmade in USA. also CLEAN SLATE MAKEUP TOWEL IN big font on front under logo sign with light colored pink lips after 'CLEAN SLATE" but have no idea about fonts, graphics, placement or design. Want it classy, elegant, girly! COLORS LIGHT BEIGER BACKGROUND WITH BLACK WRITING/ DESIGNS

Font styles to use
Serif
Decorative
Script

Colors
fff3d1

Requirements
Must have
• Black cream girly , also state in big writing that it's a " clean slate makeup towel" with a tiny light pink lip between the show and makeup. Include www.petalcharmtowel.com Brightwater Fenn, LLC
Nice to have
• Perhaps an outline of a little black dress. A black scroll edge of some sort around card. Classy

```html
<!DOCTYPE html>
<html lang="en">
<head>
<meta charset="utf-8">
<title>Petal Charm Towel – Hang Tag</title>
<link href="https://fonts.googleapis.com/css2?family=Kaushan+Script&family=Dancing+Script:wght@600&family=Josefin+Sans:wght@300;400&family=Open+Sans:wght@600&display=swap" rel="stylesheet">
<style>
  :root {
    --backdrop: #e9e6e2;
    --frame-grey: #5a5350;
    --cream: #fff3d1;
    --ink: #141214;
    --band: #000000;
    --band-text: #ffffff;
    --lip-pink: #f2a7b8;
    --towel-black: #1c1a1c;
  }
  html, body {
    margin: 0;
    width: 1200px;
    height: 873px;
    overflow: hidden;
    background: var(--backdrop);
  }
  .canvas {
    position: relative;
    width: 1200px;
    height: 873px;
  }
  .tag {
    position: absolute;
    top: 286px;
    width: 520px;
    height: 300px;
    background: var(--frame-grey);
    box-shadow: 0 6px 18px rgba(0,0,0,.18);
    overflow: hidden;
  }
  .tag--back { left: 50px; }
  .tag--front { left: 630px; }
  .tag__frame {
    position: absolute;
    inset: 0;
  }
  .tag__band {
    position: absolute;
    left: 0;
    right: 0;
    top: 240px;
    height: 26px;
    background: var(--band);
    color: var(--band-text);
    font-family: "Open Sans", sans-serif;
    font-weight: 600;
    font-size: 13px;
    letter-spacing: .06em;
    text-align: center;
    line-height: 26px;
    white-space: nowrap;
  }
  .tag__made {
    position: absolute;
    left: 0; right: 0;
    top: 270px;
    text-align: center;
    font-family: "Dancing Script", cursive;
    font-size: 17px;
    line-height: 22px;
    color: var(--cream);
  }

  /* back */
  .brand {
    position: absolute;
    left: 40px; right: 40px;
    top: 30px;
    text-align: center;
    font-family: "Josefin Sans", sans-serif;
    font-weight: 300;
    font-size: 26px;
    line-height: 32px;
    letter-spacing: .14em;
    white-space: nowrap;
    color: var(--ink);
  }
  .brand__tm { font-size: 11px; vertical-align: super; letter-spacing: 0; }
  .brand__sub {
    position: absolute;
    left: 0; right: 0;
    top: 68px;
    text-align: center;
    font-family: "Josefin Sans", sans-serif;
    font-size: 9px;
    line-height: 12px;
    letter-spacing: .12em;
    white-space: nowrap;
    color: var(--ink);
  }
  .rule {
    position: absolute;
    height: 1px;
    background: var(--ink);
  }
  .rule--top { left: 110px; width: 300px; top: 88px; }
  .rule--bottom { left: 110px; width: 300px; top: 212px; }
  .story {
    position: absolute;
    left: 40px; right: 40px;
    top: 96px;
    margin: 0;
    text-align: center;
    font-family: "Dancing Script", cursive;
    font-size: 19px;
    line-height: 27px;
    white-space: nowrap;
    color: var(--ink);
  }

  /* front */
  .headline {
    position: absolute;
    font-family: "Kaushan Script", cursive;
    color: var(--ink);
    margin: 0;
    font-weight: 400;
    line-height: 1.2;
    white-space: nowrap;
  }
  .headline--top { left: 52px; top: 22px; font-size: 48px; }
  .lips {
    position: absolute;
    left: 132px;
    top: 98px;
    width: 50px;
    height: 24px;
    border-radius: 50%;
    background: var(--lip-pink);
  }
  .headline--bottom { left: 40px; top: 128px; font-size: 42px; }
  .towel {
    position: absolute;
    left: 318px;
    top: 92px;
    width: 118px;
    height: 128px;
    border-radius: 30px 30px 14px 14px;
    background: linear-gradient(160deg, #3a363a, var(--towel-black));
  }
  .hair-tie {
    position: absolute;
    left: 440px;
    top: 118px;
    width: 54px;
    text-align: center;
    font-family: "Dancing Script", cursive;
    font-size: 14px;
    line-height: 16px;
    color: var(--ink);
  }
</style>
</head>
<body>
<main class="canvas">

  <section class="tag tag--back">
    <svg class="tag__frame" width="520" height="300" viewBox="0 0 520 300" aria-hidden="true">
      <path d="M38,6 H482 A22,22 0 0 0 506,30 V218 A22,22 0 0 0 482,242 H38 A22,22 0 0 0 14,218 V30 A22,22 0 0 0 38,6 Z"
            fill="none" stroke="var(--cream)" stroke-width="3" stroke-linecap="round" stroke-dasharray="0 8"/>
      <path d="M44,16 H476 A20,20 0 0 0 496,36 V212 A20,20 0 0 0 476,232 H44 A20,20 0 0 0 24,212 V36 A20,20 0 0 0 44,16 Z"
            fill="var(--cream)"/>
    </svg>
    <div class="brand">PETAL CHARM TOWEL<span class="brand__tm">™</span></div>
    <div class="brand__sub">CLEAN SLATE MAKEUP TOWEL</div>
    <div class="rule rule--top"></div>
    <p class="story">The essential to every girl's wardrobe.<br>So when the little black dress comes off,<br>our PETAL CHARM TOWEL is there to<br>help you wash your day away.</p>
    <div class="rule rule--bottom"></div>
    <div class="tag__band">THE ORIGINAL CLEAN SLATE MAKEUP TOWEL</div>
    <div class="tag__made">Handmade in USA</div>
  </section>

  <section class="tag tag--front">
    <svg class="tag__frame" width="520" height="300" viewBox="0 0 520 300" aria-hidden="true">
      <path d="M38,6 H482 A22,22 0 0 0 506,30 V218 A22,22 0 0 0 482,242 H38 A22,22 0 0 0 14,218 V30 A22,22 0 0 0 38,6 Z"
            fill="none" stroke="var(--cream)" stroke-width="3" stroke-linecap="round" stroke-dasharray="0 8"/>
      <path d="M44,16 H476 A20,20 0 0 0 496,36 V212 A20,20 0 0 0 476,232 H44 A20,20 0 0 0 24,212 V36 A20,20 0 0 0 44,16 Z"
            fill="var(--cream)"/>
    </svg>
    <h1 class="headline headline--top">Clean Slate</h1>
    <div class="lips" role="img" aria-label="Light pink lips illustration"></div>
    <h2 class="headline headline--bottom">Makeup Towel</h2>
    <div class="towel" role="img" aria-label="Photo of the black towel folded into a little black dress"></div>
    <div class="hair-tie">Built in a Hair Tie!</div>
    <div class="tag__band">WWW.PETALCHARMTOWEL.COM</div>
  </section>

</main>
</body>
</html>
```